Firm Stationery Design

I need a design for stationery, including: Stationery First Page, Stationery Second Sheet, Envelope, Mailing Label for Flat Envelopes, and Business Cards

```html
<!DOCTYPE html>
<html lang="en">
<head>
<meta charset="utf-8">
<title>Harlow Law — Stationery Set</title>
<link href="https://fonts.googleapis.com/css2?family=Arimo:wght@400;700&display=swap" rel="stylesheet">
<style>
  :root{
    --bg:#3a3b3d;
    --paper:#f5f3f3;
    --white:#ffffff;
    --ink:#1d1d1d;
    --text:#4a4a4a;
    --accent:#f59b00;
    --dark-card:#2e2e2e;
    --tint-grey:#e3e2e2;
    --tint-peach:#f6eadb;
  }
  *{box-sizing:border-box;margin:0;padding:0}
  html,body{width:1200px;height:597px;overflow:hidden;background:var(--bg);font-family:"Arimo",Arial,sans-serif;color:var(--text)}
  .canvas{position:relative;width:1200px;height:597px}
  .sheet{position:absolute;overflow:hidden;box-shadow:0 2px 8px rgba(0,0,0,.35)}

  /* brand lockup */
  .brand{display:flex;align-items:center;gap:.35em;font-weight:700;color:var(--ink);white-space:nowrap;line-height:1}
  .brand-square{display:inline-block;width:.7em;height:.7em;background:var(--accent)}
  .brand--light{color:var(--white)}

  /* contact list */
  .contact{font-size:5.6px;line-height:7.4px;color:var(--text)}
  .contact .addr{margin-bottom:2px}
  .contact li{list-style:none;display:flex;align-items:center;gap:3px}
  .contact svg{width:5px;height:5px;fill:var(--accent);flex:none}

  /* business card front */
  .card-front{left:44px;top:120px;width:256px;height:146px;background:var(--white);border-radius:10px}
  .card-front .brand{position:absolute;left:22px;top:64px;font-size:15px}
  .card-front .divider{position:absolute;left:128px;top:32px;width:1px;height:82px;background:#cfcfcf}
  .card-front .person{position:absolute;left:137px;top:35px}
  .card-front .name{font-size:10px;font-weight:700;color:var(--ink);letter-spacing:.2px}
  .card-front .role{font-size:5.4px;color:var(--accent);margin-top:2px}
  .card-front .contact{position:absolute;left:137px;top:59px;font-size:6px;line-height:7.6px}

  /* business card back */
  .card-back{left:39px;top:322px;width:262px;height:148px;background:var(--dark-card);border-radius:8px;display:flex;align-items:center;justify-content:center}
  .card-back .brand{font-size:20px}

  /* letterhead */
  .letterhead{left:327px;top:52px;width:358px;height:505px;background:var(--paper)}
  .letterhead .brand{position:absolute;left:34px;top:62px;font-size:12px}
  .letterhead .contact{position:absolute;left:252px;top:33px}
  .letterhead .tint{position:absolute}
  .letterhead .tint--grey{left:55px;top:136px;width:98px;height:232px;background:var(--tint-grey);opacity:.75}
  .letterhead .tint--peach{left:168px;top:136px;width:110px;height:232px;background:var(--tint-peach);opacity:.75}
  .letter{position:absolute;left:36px;top:124px;width:289px}
  .letter .salutation{font-size:9.6px;color:#555;margin-bottom:14px}
  .letter p{font-size:5.1px;line-height:8.6px;text-align:justify;margin-bottom:8.6px;color:#5a5a5a}
  .letter .closing{margin-top:16px}
  .signature{width:46px;height:18px;margin:6px 0 5px;background:linear-gradient(90deg,rgba(30,30,30,.12),rgba(30,30,30,.04))}
  .letter .signer{font-size:7.6px;color:#555}
  .letter .signer-role{font-size:5.8px;color:#666;margin-top:2px}

  /* mailing label */
  .label{left:752px;top:77px;width:364px;height:99px;background:var(--paper)}
  .label .brand{position:absolute;left:22px;top:42px;font-size:11.5px}
  .label .divider{position:absolute;left:101px;top:22px;width:1px;height:55px;background:var(--ink)}
  .label .contact{position:absolute;left:116px;top:23px;font-size:6.2px;line-height:8px}
  .label .tint--grey{position:absolute;left:258px;top:2px;width:55px;height:95px;background:var(--tint-grey)}
  .label .tint--peach{position:absolute;left:316px;top:2px;width:46px;height:95px;background:var(--tint-peach)}

  /* envelope back with flap */
  .envelope-back{left:746px;top:236px;width:401px;height:183px;background:var(--paper)}
  .envelope-back svg.flap{position:absolute;left:0;top:0}
  .envelope-back .brand{position:absolute;left:0;right:0;top:26px;justify-content:center;font-size:15px}

  /* envelope front */
  .envelope-front{left:716px;top:333px;width:403px;height:183px;background:var(--paper)}
  .envelope-front .brand{position:absolute;left:24px;top:64px;font-size:11.5px}
  .envelope-front .contact{position:absolute;left:24px;top:117px;font-size:5.8px;line-height:7.4px}
  .envelope-front .tint--grey{position:absolute;left:211px;top:5px;width:100px;height:173px;background:var(--tint-grey)}
  .envelope-front .tint--peach{position:absolute;left:284px;top:5px;width:110px;height:173px;background:var(--tint-peach)}
</style>
</head>
<body>
<svg width="0" height="0" style="position:absolute" aria-hidden="true">
  <defs>
    <symbol id="icon-phone" viewBox="0 0 10 10"><path d="M2 0.5l2 2.2-1 1.2c.6 1.3 1.6 2.3 2.9 2.9l1.2-1 2.2 2-1.2 1.7C4.4 9.3.7 5.6.3 1.7z"/></symbol>
    <symbol id="icon-mobile" viewBox="0 0 10 10"><path d="M2.5 0h5v10h-5zM3.5 1v7h3V1z"/></symbol>
    <symbol id="icon-mail" viewBox="0 0 10 10"><path d="M0 2h10v6H0zM1 3l4 2.6L9 3z" fill-rule="evenodd"/></symbol>
    <symbol id="icon-web" viewBox="0 0 10 10"><circle cx="5" cy="5" r="5"/></symbol>
  </defs>
</svg>

<main class="canvas">

  <!-- Business card, front -->
  <section class="sheet card-front" aria-label="Business card front">
    <div class="brand"><span>Harlow Law</span><span class="brand-square"></span></div>
    <div class="divider"></div>
    <div class="person">
      <div class="name">DANIEL REYES</div>
      <div class="role">President</div>
    </div>
    <ul class="contact">
      <div class="addr">412 Maple Crest Road<br>Halden, Canada 20817</div>
      <li><svg><use href="#icon-phone"/></svg>555-201-4410</li>
      <li><svg><use href="#icon-mobile"/></svg>555-201-4422</li>
      <li><svg><use href="#icon-mail"/></svg>hello@harlowlaw.com</li>
      <li><svg><use href="#icon-web"/></svg>www.harlowlaw.com</li>
    </ul>
  </section>

  <!-- Business card, back -->
  <section class="sheet card-back" aria-label="Business card back">
    <div class="brand brand--light"><span>Harlow Law</span><span class="brand-square"></span></div>
  </section>

  <!-- Letterhead -->
  <section class="sheet letterhead" aria-label="Letterhead first page">
    <div class="tint tint--grey"></div>
    <div class="tint tint--peach"></div>
    <div class="brand"><span>Harlow Law</span><span class="brand-square"></span></div>
    <ul class="contact">
      <div class="addr">412 Maple Crest Road<br>Halden, Canada 20817</div>
      <li><svg><use href="#icon-phone"/></svg>555-201-4410</li>
      <li><svg><use href="#icon-mobile"/></svg>555-201-4422</li>
      <li><svg><use href="#icon-mail"/></svg>hello@harlowlaw.com</li>
      <li><svg><use href="#icon-web"/></svg>www.harlowlaw.com</li>
    </ul>
    <article class="letter">
      <div class="salutation">Dear Mr. Reyes,</div>
      <p>Lorem ipsum dolor sit amet, consectetur adipiscing elit. Donec orci purus, luctus vitae dignissim eu, iaculis sed purus. Vivamus faucibus, ipsum nec aliquet viverra, leo mauris condimentum ligula, sit amet sagittis enim ligula quis arcu. Nam egestas tortor id nisi porttitor mattis. In tortor ante, ultricies in suscipit a, tempus non massa. Vivamus et auctor mi. Fusce vel massa nulla. Phasellus nec eros mauris, et scelerisque orci.</p>
      <p>Donec malesuada orci vitae nulla accumsan porta a id massa. Quisque accumsan iaculis magna sit amet fringilla. Maecenas consequat, magna eget tincidunt semper, odio nibh rutrum mi, id feugiat ante nisi eu risus. Vestibulum nunc orci, rhoncus a placerat in, ultricies in mi. Cras mattis varius eros, vel fringilla nisi suscipit eget. Quisque scelerisque sagittis nulla at porttitor.</p>
      <p>Sed id augue vitae urna euismod commodo aliquet a quam. Pellentesque arcu velit, cursus et malesuada ut, consequat et diam. Nullam erat sem, rhoncus id ullamcorper vitae, rhoncus et arcu. In ultricies ultricies nulla, ut rutrum nisi iaculis at. Donec eu magna a metus ornare faucibus. Fusce aliquet faucibus ultricies. Morbi semper, est id tincidunt gravida, sem arcu adipiscing lacus, ac bibendum nulla leo eu purus. Quisque nec diam sed risus consectetur accumsan quis quis nibh. Vestibulum id purus lorem.</p>
      <p>It is a long established fact that a reader will be distracted by the readable content of a page when looking at its layout. The point of using Lorem Ipsum is that it has a more-or-less normal distribution of letters, as opposed to using 'Content here, content here', making it look like readable English. Many desktop publishing packages</p>
      <p class="closing">Sincerely,</p>
      <div class="signature" role="img" aria-label="Handwritten signature"></div>
      <div class="signer">Daniel Reyes</div>
      <div class="signer-role">CEO/ Founder</div>
    </article>
  </section>

  <!-- Mailing label -->
  <section class="sheet label" aria-label="Mailing label">
    <div class="brand"><span>Harlow Law</span><span class="brand-square"></span></div>
    <div class="divider"></div>
    <ul class="contact">
      <div class="addr">412 Maple Crest Road<br>Halden, Canada 20817</div>
      <li><svg><use href="#icon-phone"/></svg>555-201-4410</li>
      <li><svg><use href="#icon-mobile"/></svg>555-201-4422</li>
      <li><svg><use href="#icon-mail"/></svg>hello@harlowlaw.com</li>
      <li><svg><use href="#icon-web"/></svg>www.harlowlaw.com</li>
    </ul>
    <div class="tint--grey"></div>
    <div class="tint--peach"></div>
  </section>

  <!-- Envelope, back with flap -->
  <section class="sheet envelope-back" aria-label="Envelope back">
    <svg class="flap" width="401" height="70" viewBox="0 0 401 70" aria-hidden="true">
      <path d="M0 0H401L393 40Q388 66 360 66H40Q12 66 7 40Z" fill="#1e1e1e"/>
    </svg>
    <div class="brand brand--light"><span>Harlow Law</span><span class="brand-square"></span></div>
  </section>

  <!-- Envelope, front -->
  <section class="sheet envelope-front" aria-label="Envelope front">
    <div class="tint--grey"></div>
    <div class="tint--peach"></div>
    <div class="brand"><span>Harlow Law</span><span class="brand-square"></span></div>
    <ul class="contact">
      <div class="addr">412 Maple Crest Road<br>Halden, Canada 20817</div>
      <li><svg><use href="#icon-phone"/></svg>555-201-4410</li>
      <li><svg><use href="#icon-mobile"/></svg>555-201-4422</li>
      <li><svg><use href="#icon-mail"/></svg>hello@harlowlaw.com</li>
      <li><svg><use href="#icon-web"/></svg>www.harlowlaw.com</li>
    </ul>
  </section>

</main>
</body>
</html>
```